MCLS Banner

We need a design for a pull-up banner (850 x 2000 mm) to promote the Merida Cable Ledger Scheme. https://mclsnet.info/en/
The banner action should be to get people to scan a QR code to join a mailing list (add a frame to add the QR code)

Use the website colours and typology https://mclsnet.info/en/
See also brochure for ideas https://mclsnet.info/documents/9/MCLS_brochure_english.pdf

```html
<!DOCTYPE html>
<html lang="en">
<head>
<meta charset="utf-8">
<title>MCLS Pull-up Banner</title>
<link rel="stylesheet" href="https://fonts.googleapis.com/css2?family=Montserrat:wght@400;500;700;800&display=swap">
<style>
  :root{
    --navy:#0e0c22;
    --lime:#bcd22e;
    --blue:#3391d6;
    --ink:#2b2b33;
    --stage:#ececec;
    --panel-light:#fafafa;
    --panel-mid:#e3e4e6;
    --panel-dark:#c9cacd;
    --map-dark:#161616;
  }
  *{margin:0;padding:0;box-sizing:border-box}
  html,body{width:1200px;height:1200px;overflow:hidden;background:var(--stage)}
  body{position:relative;font-family:"Montserrat",sans-serif}

  .banner{
    position:absolute;left:347px;top:10px;width:506px;height:1180px;overflow:hidden;
    background:radial-gradient(ellipse 70% 45% at 50% 50%,var(--panel-light) 0%,var(--panel-mid) 75%,var(--panel-dark) 100%);
    box-shadow:0 2px 10px rgba(0,0,0,.12);
  }
  .network-top{
    position:absolute;left:0;top:0;width:100%;height:340px;
    background:radial-gradient(ellipse 60% 55% at 35% 30%,rgba(255,255,255,.55),rgba(255,255,255,0) 70%),
               linear-gradient(180deg,var(--panel-dark) 0%,rgba(227,228,230,0) 100%);
  }
  .network-bottom{
    position:absolute;left:0;top:960px;width:100%;height:220px;
    background:linear-gradient(180deg,rgba(201,202,205,0) 0%,rgba(201,202,205,.6) 100%);
  }
  .brand-name{
    position:absolute;right:26px;top:186px;
    font-weight:700;font-size:112px;line-height:1;letter-spacing:-2px;color:var(--navy);
  }
  .headline{position:absolute;left:0;top:358px;width:100%;text-align:center;font-weight:800;line-height:1}
  .headline-top{font-size:38px;color:var(--navy)}
  .headline-band{
    display:block;margin:8px 14px 0;height:40px;background:var(--navy);
    color:var(--lime);font-size:41px;line-height:40px;letter-spacing:.3px;
  }
  .headline-accent{display:block;margin-top:10px;font-size:42px;color:var(--blue)}
  .rule{position:absolute;left:72px;top:507px;width:363px;height:3px;background:var(--navy)}
  .scheme-name{
    position:absolute;left:0;top:516px;width:100%;text-align:center;
    font-weight:400;font-size:23px;color:var(--ink);letter-spacing:.2px;
  }
  .tagline{
    position:absolute;left:0;top:576px;width:100%;text-align:center;
    font-weight:500;font-size:19.5px;line-height:28px;color:var(--navy);
  }
  .map-ring{
    position:absolute;left:42px;top:650px;width:422px;height:422px;border-radius:50%;
    background:rgba(235,236,238,.9);box-shadow:0 0 18px rgba(0,0,0,.05);
  }
  .map-disc{
    position:absolute;left:56px;top:664px;width:394px;height:394px;border-radius:50%;
    background:radial-gradient(circle at 55% 45%,#2a241c 0%,var(--map-dark) 70%);
  }
  .contact-band{
    position:absolute;left:0;top:1088px;width:100%;height:42px;background:var(--navy);
    display:flex;align-items:center;justify-content:center;gap:10px;padding:0 12px;
    font-weight:700;font-size:19px;white-space:nowrap;
  }
  .contact-email{color:var(--lime)}
  .contact-sep{color:var(--lime);font-weight:500}
  .contact-web{color:var(--blue)}
</style>
</head>
<body>
  <main class="banner">
    <div class="network-top" role="img" aria-label="Faint white network of connected dots and lines"></div>
    <div class="network-bottom" role="img" aria-label="Faint grey network of connected dots and lines"></div>

    <div class="brand-name">mcls</div>

    <h1 class="headline">
      <span class="headline-top">MAPPING THE</span>
      <span class="headline-band">WORLD'S INTERNET</span>
      <span class="headline-accent">BACKBONE.</span>
    </h1>

    <div class="rule"></div>
    <p class="scheme-name">Merida Cable Ledger Scheme</p>

    <p class="tagline">A community-driven solution for<br>mapping the world's Internet backbone</p>

    <div class="map-ring"></div>
    <div class="map-disc" role="img" aria-label="Dark map of Central Africa showing orange terrestrial fibre routes and blue submarine cables"></div>

    <footer class="contact-band">
      <span class="contact-email">outreach@mclsnet.info</span>
      <span class="contact-sep">|</span>
      <span class="contact-web">www.mclsnet.info</span>
    </footer>
  </main>
</body>
</html>
```